Quenvale Capital LLC

Need Professional Business cards for New Investment Fund

Target Market(s)

High Quality investors

Industry/Entity Type

Financial

Contact Information for Business Card

Phone Number +1 555 284 6190
Name Lukas Varenko
Title Fund Manager
email lv@FundQuenvale.com
Website www.FundQuenvale.com

Colors

Designer to choose colors to be used in the design.

Requirements
Must have
• Must have our Logo and all of the above. Must be made so lettering and loge can be raised

```html
<!DOCTYPE html>
<html lang="en">
<head>
<meta charset="UTF-8">
<title>Quenvale Capital LLC – Business Card</title>
<link href="https://fonts.googleapis.com/css2?family=Montserrat:wght@400;500;700&display=swap" rel="stylesheet">
<style>
  :root {
    --backdrop: #3a2e29;
    --card: #333435;
    --card-mark: #3b3c3e;
    --accent: #35e02a;
    --ink: #f2f2f2;
    --rule: #d9d9d9;
  }
  * { margin: 0; padding: 0; box-sizing: border-box; }
  html, body {
    width: 1200px; height: 800px; overflow: hidden;
    background: var(--backdrop);
    font-family: "Montserrat", sans-serif;
  }
  .stage {
    width: 1200px; height: 800px;
    display: flex; align-items: center; justify-content: center; gap: 40px;
  }
  .card {
    position: relative;
    width: 540px; height: 309px;
    background: var(--card);
    border: 2px solid var(--accent);
    border-radius: 2px;
    box-shadow: 0 6px 18px rgba(0,0,0,.35);
  }
  .card--front {
    display: flex; align-items: center; justify-content: center;
  }
  .front-mark {
    font-weight: 700; font-size: 36px; letter-spacing: 5px;
    color: var(--card-mark);
    text-transform: uppercase;
  }
  .brand {
    position: absolute; right: 36px; top: 96px;
    display: flex; align-items: center; gap: 10px;
  }
  .brand__square { width: 14px; height: 14px; background: var(--accent); flex: none; }
  .brand__name {
    font-weight: 700; font-size: 20px; letter-spacing: 2px;
    color: var(--ink); text-transform: uppercase; line-height: 1;
  }
  .holder { position: absolute; left: 40px; top: 104px; }
  .holder__name {
    font-weight: 700; font-size: 17px; letter-spacing: 1px;
    color: var(--accent); text-transform: uppercase; line-height: 1.2;
  }
  .holder__title {
    font-weight: 400; font-size: 12px; color: var(--ink); margin-top: 3px;
  }
  .rule {
    position: absolute; left: 40px; right: 34px; top: 150px;
    height: 1px; background: var(--rule);
  }
  .contacts {
    position: absolute; left: 40px; top: 172px;
    list-style: none;
  }
  .contacts__item {
    display: flex; align-items: center; gap: 9px;
    font-size: 13px; color: var(--ink); margin-bottom: 8px;
  }
  .contacts__icon { width: 12px; height: 12px; flex: none; }
</style>
</head>
<body>
<main class="stage">
  <section class="card card--front" aria-label="Card front">
    <span class="front-mark">Quenvale</span>
  </section>

  <section class="card card--back" aria-label="Card back">
    <div class="brand">
      <span class="brand__square"></span>
      <span class="brand__name">Quenvale</span>
    </div>

    <div class="holder">
      <p class="holder__name">Lukas Varenko</p>
      <p class="holder__title">Fund Manager</p>
    </div>

    <div class="rule"></div>

    <ul class="contacts">
      <li class="contacts__item">
        <svg class="contacts__icon" viewBox="0 0 24 24" aria-hidden="true">
          <path fill="#35e02a" d="M6.6 10.8a15.1 15.1 0 0 0 6.6 6.6l2.2-2.2a1 1 0 0 1 1-.25 11.4 11.4 0 0 0 3.6.57 1 1 0 0 1 1 1V20a1 1 0 0 1-1 1A17 17 0 0 1 3 4a1 1 0 0 1 1-1h3.5a1 1 0 0 1 1 1c0 1.250.2 2.450.57 3.6a1 1 0 0 1-.25 1z"/>
        </svg>
        <span>+1 555 284 6190</span>
      </li>
      <li class="contacts__item">
        <svg class="contacts__icon" viewBox="0 0 24 24" aria-hidden="true">
          <rect x="2" y="5" width="20" height="14" rx="2" fill="#35e02a"/>
          <path d="M3 6l9 7 9-7" fill="none" stroke="#333435" stroke-width="2"/>
        </svg>
        <span>lv@FundQuenvale.com</span>
      </li>
      <li class="contacts__item">
        <svg class="contacts__icon" viewBox="0 0 24 24" aria-hidden="true">
          <circle cx="12" cy="12" r="10" fill="#35e02a"/>
          <path d="M2 12h20M12 2c3 3 3 17 0 20M12 2c-3 3-3 17 0 20" fill="none" stroke="#333435" stroke-width="1.6"/>
        </svg>
        <span>www.FundQuenvale.com</span>
      </li>
    </ul>
  </section>
</main>
</body>
</html>
```